Gobal construction supply company needs new business card design

I need a business card design for my global supply company using an existing logo. i will be looking to print these on rounded corner cards with the black background version of my logo on the back. on the front white background, my logo again and my simple details.

```html
<!DOCTYPE html>
<html lang="en">
<head>
<meta charset="utf-8">
<title>Continental Building Supplies – Business Card</title>
<link rel="stylesheet" href="https://fonts.googleapis.com/css2?family=Open+Sans:wght@400;600;700&display=swap">
<style>
  :root {
    --backdrop: #7b7b7b;
    --card-light: #f3f3f3;
    --card-dark: #1c1c1c;
    --ink: #1a1a1a;
    --ink-soft: #2b2b2b;
    --brand-red: #d90f0f;
    --paper-white: #ffffff;
  }
  * { box-sizing: border-box; margin: 0; padding: 0; }
  html, body {
    width: 1200px; height: 900px; overflow: hidden;
    background: var(--backdrop);
    font-family: "Open Sans", Arial, sans-serif;
  }
  .canvas { position: relative; width: 1200px; height: 900px; }

  .card {
    position: absolute; top: 200px; width: 310px; height: 502px;
  }
  .card--front {
    left: 253px; background: var(--card-light);
    border-radius: 56px 0 56px 0;
  }
  .card--back {
    left: 627px; background: var(--card-dark);
    border-radius: 0 56px 0 56px;
  }

  .brand {
    position: absolute; left: 0; right: 0;
    display: flex; flex-direction: column; align-items: center;
  }
  .card--front .brand { top: 92px; }
  .card--back .brand { top: 198px; }
  .brand__dot {
    width: 20px; height: 20px; border-radius: 50%;
    background: var(--brand-red); margin-bottom: 18px;
  }
  .brand__name {
    font-weight: 700; font-size: 19px; line-height: 23px;
    text-align: center; letter-spacing: 0.2px;
  }
  .card--front .brand__name { color: var(--ink); }
  .card--back .brand__name { color: var(--paper-white); }

  .contact { position: absolute; left: 33px; top: 293px; color: var(--ink-soft); }
  .contact__name {
    color: var(--brand-red); font-weight: 700; font-size: 18.5px; line-height: 22px;
  }
  .contact__role { font-size: 14.5px; line-height: 20px; margin-bottom: 6px; }
  .contact__list { list-style: none; }
  .contact__item {
    display: flex; align-items: center; gap: 6px;
    font-size: 14.5px; line-height: 18.5px;
  }
  .contact__icon { width: 12px; height: 12px; fill: var(--brand-red); flex: none; }
  .contact__address { font-size: 14.5px; line-height: 18.5px; margin-top: 7px; }

  .back__site {
    position: absolute; left: 0; right: 0; top: 439px;
    text-align: center; color: var(--paper-white);
    font-size: 13px; font-weight: 600; letter-spacing: 0.6px;
  }
</style>
</head>
<body>
<main class="canvas">

  <section class="card card--front" aria-label="Card front">
    <div class="brand">
      <span class="brand__dot"></span>
      <p class="brand__name">CONTINENTAL BUILDING<br>SUPPLIES</p>
    </div>

    <div class="contact">
      <h1 class="contact__name">DANIEL MARSH</h1>
      <p class="contact__role">Managing Director</p>
      <ul class="contact__list">
        <li class="contact__item">
          <svg class="contact__icon" viewBox="0 0 12 12"><path d="M1 4.5C1 3 3 2 6 2s5 1 5 2.5V6H8.5V4.8h-5V6H1z"/><rect x="2" y="6.5" width="8" height="4" rx="1"/></svg>
          055-987 654 321
        </li>
        <li class="contact__item">
          <svg class="contact__icon" viewBox="0 0 12 12"><path d="M3.5 0.5h5a1 1 0 0 1 1 1v9a1 1 0 0 1-1 1h-5a1 1 0 0 1-1-1v-9a1 1 0 0 1 1-1zM4 2v7h4V2z"/></svg>
          055-987 654 321
        </li>
        <li class="contact__item">
          <svg class="contact__icon" viewBox="0 0 12 12"><path d="M1 3h10v6.5H1z M1.6 3.4L6 6.8l4.4-3.4" stroke="#f3f3f3" stroke-width="0.9"/></svg>
          hello@mailname.com
        </li>
        <li class="contact__item">
          <svg class="contact__icon" viewBox="0 0 12 12"><circle cx="6" cy="6" r="5.2"/><path d="M3.5 4.2l1.8.4.6 1.6-1.2 1.4.4 2M7.2 2.2l.6 1.6 1.8.3" stroke="#f3f3f3" stroke-width="0.8" fill="none"/></svg>
          www.yoursitename.com
        </li>
      </ul>
      <p class="contact__address">67890, Street Name Here<br>Region Name, 654321.</p>
    </div>
  </section>

  <section class="card card--back" aria-label="Card back">
    <div class="brand">
      <span class="brand__dot"></span>
      <p class="brand__name">CONTINENTAL BUILDING<br>SUPPLIES</p>
    </div>
    <p class="back__site">www.yoursitename.com</p>
  </section>

</main>
</body>
</html>
```